Structural Engineering Business Card

Brookvane Drafting does residential house plans for clients in Central Florida. Would like simple but elegant business card that is appropriate for a house plan engineering company. Prefer black business card with black/white them but open to other shades of blue. I uploaded a sample card that I came across that looked good but please come up with your own creative designs.

Contact Information for Business Card

Name, Title, Phone, Email, Address, website

```html
<!DOCTYPE html>
<html lang="en">
<head>
<meta charset="utf-8">
<title>Brookvane Drafting — Business Card</title>
<link href="https://fonts.googleapis.com/css2?family=Arimo:wght@400;700&display=swap" rel="stylesheet">
<style>
  :root {
    --backdrop: #e9e9e9;
    --card: #333333;
    --card-shade: #454545;
    --ink: #ffffff;
    --ink-soft: #e6e6e6;
  }
  * { box-sizing: border-box; margin: 0; padding: 0; }
  html, body {
    width: 1200px; height: 802px; overflow: hidden;
    background: var(--backdrop);
    font-family: "Arimo", Arial, sans-serif;
  }
  .sheet {
    position: relative; width: 1200px; height: 802px;
    display: flex; align-items: center; justify-content: center; gap: 60px;
  }
  .card {
    position: relative; width: 520px; height: 297px;
    background: var(--card); color: var(--ink); overflow: hidden;
    box-shadow: 0 8px 24px rgba(0,0,0,.18);
  }
  .card__decor {
    position: absolute; right: 0; top: 0; width: 62%; height: 58%;
    background: linear-gradient(160deg, var(--card-shade) 0%, rgba(69,69,69,0) 85%);
  }
  .wordmark {
    font-weight: 700; color: var(--ink); letter-spacing: .5px; line-height: 1;
    text-transform: uppercase;
  }
  .card--front .wordmark { position: absolute; left: 36px; top: 42px; font-size: 26px; }
  .address {
    position: absolute; right: 34px; top: 42px; text-align: right;
    font-size: 14px; line-height: 1.35; color: var(--ink-soft);
  }
  .person { position: absolute; left: 36px; top: 130px; }
  .person__name { font-weight: 700; font-size: 19px; letter-spacing: .5px; text-transform: uppercase; }
  .person__title { font-size: 13px; color: var(--ink-soft); margin-top: 2px; }
  .contacts { position: absolute; left: 36px; top: 190px; list-style: none; }
  .contacts li {
    display: flex; align-items: center; gap: 9px;
    font-size: 14px; line-height: 1; margin-bottom: 8px; color: var(--ink-soft);
  }
  .contacts svg { width: 13px; height: 13px; flex: none; }
  .card--back .wordmark {
    position: absolute; left: 0; right: 0; top: 50%; transform: translateY(-50%);
    text-align: center; font-size: 38px;
  }
</style>
</head>
<body>
<main class="sheet">
  <section class="card card--front" aria-label="Business card front">
    <div class="card__decor" role="img" aria-label="Faint brand decoration"></div>
    <div class="wordmark">Brookvane Drafting</div>
    <address class="address" style="font-style:normal">Your Address<br>City, State, Zip 0000</address>
    <div class="person">
      <div class="person__name">Marcus Ellery</div>
      <div class="person__title">Manager</div>
    </div>
    <ul class="contacts">
      <li>
        <svg viewBox="0 0 16 16" aria-hidden="true"><path fill="#fff" d="M3.5 1.5l2.5 2.6-1.3 1.8c.9 2 2.4 3.5 4.4 4.4l1.8-1.3 2.6 2.5-1.6 2.5C7 13.6 2.4 9 1 3.1z"/></svg>
        555-214-7730
      </li>
      <li>
        <svg viewBox="0 0 16 16" aria-hidden="true"><rect x="1" y="3" width="14" height="10" fill="#fff"/><path d="M1 3l7 6 7-6" fill="none" stroke="#333" stroke-width="1.4"/></svg>
        marcus@brookvanedrafting.com
      </li>
      <li>
        <svg viewBox="0 0 16 16" aria-hidden="true"><circle cx="8" cy="8" r="7" fill="#fff"/><path d="M1 8h14M8 1c-3 3.5-3 10.5 0 14M8 1c3 3.5 3 10.5 0 14" fill="none" stroke="#333" stroke-width="1.1"/></svg>
        www.brookvanedrafting.com
      </li>
    </ul>
  </section>

  <section class="card card--back" aria-label="Business card back">
    <div class="card__decor" role="img" aria-label="Faint brand decoration"></div>
    <div class="wordmark">Brookvane Drafting</div>
  </section>
</main>
</body>
</html>
```